Cool Website Design Gleam Shell Crew.

We need a new website, using our existing domain, with a similar function to https://www.marbeckfilm.com/ or https://www.tolvanfinishworks.com/ instagram gleam_shell.crew.
We can send google docs with pictures.
Logo attached

```html
<!DOCTYPE html>
<html lang="en">
<head>
<meta charset="utf-8">
<title>Gleam Shell Crew — Vehicle Wraps, PPF &amp; Tinting in Calgary</title>
<link rel="stylesheet" href="https://fonts.googleapis.com/css2?family=Roboto:ital,wght@0,400;0,500;0,700;1,400&family=Rubik+Dirt&display=swap">
<style>
:root{
  --bg:#141414;
  --bg-alt:#1b1b1b;
  --card:#1e1e1e;
  --text:#ffffff;
  --muted:#b5b5b5;
  --purple:#6a2bd9;
  --violet:#7a35e6;
  --blue:#1f86dc;
  --field:#181818;
  --line:#4a4a4a;
  --grad:linear-gradient(90deg,var(--purple),var(--blue));
}
*{box-sizing:border-box;margin:0;padding:0}
html,body{width:1200px;height:4115px;overflow:hidden;background:var(--bg);color:var(--text);font-family:'Roboto',Arial,sans-serif}
.page{position:relative;width:1200px;height:4115px}
.abs{position:absolute}
.display{font-family:'Rubik Dirt','Impact',sans-serif;font-variant:small-caps;font-weight:400}
.grad-text{background:var(--grad);-webkit-background-clip:text;background-clip:text;color:transparent}
.section-title{position:absolute;left:0;width:1200px;text-align:center;font-size:42px;line-height:48px}
.btn{position:absolute;display:flex;align-items:center;justify-content:center;color:#fff;font-size:15px;font-weight:500;text-decoration:none}
.btn::before{content:"";position:absolute;inset:0;background:var(--grad);transform:skewX(-28deg);z-index:0}
.btn span{position:relative}

/* nav */
.brand{left:144px;top:14px;display:flex;align-items:center;gap:10px;color:var(--violet);font-size:20px;font-weight:700}
.brand i{width:16px;height:16px;background:var(--violet);display:block}
.nav-link{top:26px;font-size:15px;font-weight:500;color:#fff}
.nav-link.active{color:var(--blue)}
.nav-link.active::after{content:"";position:absolute;left:0;right:0;top:24px;height:2px;background:var(--blue)}

/* hero */
.hero-left{left:48px;top:99px;width:566px;height:567px;background:linear-gradient(160deg,#1c1c1e 0%,#101012 60%,#18181b 100%)}
.hero-right{left:614px;top:99px;width:540px;height:567px;background:linear-gradient(180deg,#c98a6e 0%,#6f6a5a 22%,#3e4a32 38%,#4a4a46 60%,#2a2a2a 100%)}
.hero-title{left:112px;top:276px;font-size:36px;line-height:48px;color:#fff}
.hero-sub{left:112px;top:376px;width:460px;font-size:18.5px;line-height:28px}
.arrow-btn{width:50px;height:50px;border-radius:50%;background:#0d0d0d;display:flex;align-items:center;justify-content:center}

/* about */
.about-title{left:618px;top:766px;font-size:42px;line-height:48px}
.about-copy{left:618px;width:445px;font-size:15.5px;line-height:24px}
.about-copy.accent{color:var(--violet)}

/* services */
.card{position:absolute;top:1374px;width:272px;height:325px;background:linear-gradient(180deg,#222 0%,#191919 100%);text-align:center}
.card.featured{border:3px solid transparent;background:linear-gradient(#1c1c1c,#1c1c1c) padding-box,linear-gradient(135deg,var(--purple),var(--blue)) border-box}
.card svg{position:absolute;left:50%;top:54px;transform:translateX(-50%)}
.card h3{position:absolute;top:132px;left:0;right:0;font-size:20px;font-weight:500}
.card p{position:absolute;top:172px;left:36px;right:36px;font-size:15.5px;line-height:24px;color:var(--muted)}

/* gallery */
.work-sub{left:0;width:1200px;top:1938px;text-align:center;font-size:15.5px;line-height:24px;color:var(--muted)}
.photo{position:absolute}

/* testimonials */
.testi-band{left:0;top:2660px;width:1200px;height:488px;background:radial-gradient(ellipse at 50% 50%,#242428 0%,#161618 70%,#121213 100%)}
.quote-mark{font-family:Georgia,serif;font-size:110px;line-height:1;font-weight:700}
.testi-head{font-size:17px;line-height:24px}
.testi-body{font-size:14.5px;line-height:24px;color:var(--muted);font-style:italic;width:330px}
.testi-name{font-size:17px;font-weight:700}
.testi-name small{font-size:12px;font-weight:400;color:var(--muted);margin-left:8px}

/* contact form */
.field{position:absolute;border:1px solid var(--line);background:var(--field);color:#6f6f6f;font-size:14px;padding:18px 22px}

/* footer */
.footer{left:0;top:3694px;width:1200px;height:421px;background:linear-gradient(180deg,#19191b 0%,#131314 100%)}
.foot-brand{left:144px;top:3778px;display:flex;align-items:center;gap:10px;color:var(--violet);font-size:24px;font-weight:700}
.foot-brand i{width:18px;height:18px;background:var(--violet);display:block}
.foot-col h4{font-size:18px;font-weight:700;margin-bottom:14px}
.foot-col li{list-style:none;font-size:15px;line-height:24px;color:var(--muted)}
.contact-row{position:absolute;left:834px;display:flex;gap:16px;font-size:15px;line-height:24px;color:var(--muted)}
.contact-row svg{flex:none;margin-top:4px}
.copyright{left:0;width:1200px;top:4066px;text-align:center;font-size:15px}
</style>
</head>
<body>
<div class="page">

  <!-- Navigation -->
  <div class="abs brand"><i></i>Gleam Shell Crew</div>
  <a class="abs nav-link active" style="left:387px">Home</a>
  <a class="abs nav-link" style="left:459px">About</a>
  <a class="abs nav-link" style="left:529px">Services</a>
  <a class="abs nav-link" style="left:618px">Promotions</a>
  <a class="abs nav-link" style="left:727px">Gallery</a>
  <a class="abs nav-link" style="left:804px">Contact</a>
  <a class="btn" style="left:900px;top:16px;width:148px;height:40px"><span>Get A Quote</span></a>

  <!-- Hero -->
  <div class="abs hero-left" role="img" aria-label="Dark close-up of a wrapped car body"></div>
  <div class="abs hero-right" role="img" aria-label="White sports sedan on a country road at sunset"></div>
  <h1 class="abs hero-title display">Premium Vehicle Wraps,<br>PPF &amp; Tinting in Calgary</h1>
  <p class="abs hero-sub">Transform, protect, and personalize your vehicle with expert craftsmanship and premium materials.</p>
  <a class="btn" style="left:120px;top:444px;width:146px;height:39px"><span>Get A Quote</span></a>
  <a class="btn" style="left:278px;top:444px;width:150px;height:39px"><span>View Our Work</span></a>
  <div class="abs arrow-btn" style="left:18px;top:358px"><svg width="14" height="14" viewBox="0 0 14 14"><path d="M9 2 4 7l5 5" stroke="#fff" stroke-width="2" fill="none"/></svg></div>
  <div class="abs arrow-btn" style="left:1127px;top:358px"><svg width="14" height="14" viewBox="0 0 14 14"><path d="M5 2l5 5-5 5" stroke="#fff" stroke-width="2" fill="none"/></svg></div>

  <!-- About -->
  <svg class="abs" style="left:108px;top:780px" width="505" height="372" viewBox="0 0 505 372">
    <defs>
      <linearGradient id="aboutPurple" x1="0" y1="0" x2="1" y2="1"><stop offset="0" stop-color="#5a1fb0"/><stop offset="1" stop-color="#1c0b33"/></linearGradient>
      <linearGradient id="aboutBlue" x1="0" y1="0" x2="1" y2="1"><stop offset="0" stop-color="#1c9ee0"/><stop offset="1" stop-color="#0b3c63"/></linearGradient>
    </defs>
    <polygon points="16,252 120,4 362,4 158,252" fill="#2a2a2a"/>
    <polygon points="4,240 108,4 350,4 146,240" fill="url(#aboutPurple)" role="img" aria-label="Purple wrapped car hood"/>
    <polygon points="140,368 300,120 505,120 330,368" fill="#2a2a2a"/>
    <polygon points="128,368 288,128 492,128 318,368" fill="url(#aboutBlue)" role="img" aria-label="Blue wrapped car front"/>
  </svg>
  <h2 class="abs about-title display grad-text">About Us</h2>
  <p class="abs about-copy" style="top:826px">At Gleam Shell Crew, we deliver high-quality vinyl wraps, paint protection film, and tinting services designed to elevate your vehicle's look while keeping it protected.</p>
  <p class="abs about-copy" style="top:922px">We combine cutting-edge materials, precise installation, and a passion for custom automotive design to deliver flawless results—every time.</p>
  <p class="abs about-copy accent" style="top:1007px">Whether you want bold colour change wraps, subtle accents, stone-chip protection, or full custom graphics, we've got you covered.</p>
  <a class="btn" style="left:626px;top:1103px;width:148px;height:40px"><span>Learn More</span></a>

  <!-- Services -->
  <h2 class="section-title display grad-text" style="top:1294px">Our Services</h2>
  <svg width="0" height="0" class="abs"><defs><linearGradient id="iconGrad" x1="0" y1="0" x2="1" y2="1"><stop offset="0" stop-color="#6a2bd9"/><stop offset="1" stop-color="#1f86dc"/></linearGradient></defs></svg>

  <div class="card" style="left:16px">
    <svg width="60" height="60" viewBox="0 0 60 60"><path d="M14 8h34a8 8 0 0 1 0 16H42v28H22a12 12 0 0 1-12-12V16a8 8 0 0 1 4-8z" fill="url(#iconGrad)"/><circle cx="22" cy="40" r="6" fill="#1e1e1e"/></svg>
    <h3>Vinyl Wraps</h3>
    <p>Premium vinyl applied with precision for a completely new look—gloss, matte, satin, and textured finishes available.</p>
  </div>
  <div class="card featured" style="left:315px">
    <svg width="60" height="60" viewBox="0 0 60 60" style="top:51px"><rect x="10" y="10" width="40" height="44" rx="8" fill="url(#iconGrad)"/><rect x="10" y="6" width="40" height="10" rx="5" fill="#5a2ac9"/><rect x="24" y="18" width="12" height="22" rx="3" fill="#1c1c1c"/></svg>
    <h3 style="top:129px">Paint Protection Film</h3>
    <p style="top:169px">Invisible protection against chips, scratches, and road debris. Keep your paint looking brand new.</p>
  </div>
  <div class="card" style="left:614px">
    <svg width="60" height="60" viewBox="0 0 60 60"><rect x="6" y="6" width="48" height="48" fill="url(#iconGrad)"/><rect x="13" y="13" width="34" height="34" fill="none" stroke="#1e1e1e" stroke-width="3"/><path d="M16 44 44 16M26 44l18-18" stroke="#1e1e1e" stroke-width="3"/></svg>
    <h3>Window Tinting</h3>
    <p>Improve privacy, reduce heat, and give your vehicle a sleek, refined finish.</p>
  </div>
  <div class="card" style="left:911px">
    <svg width="60" height="60" viewBox="0 0 60 60"><rect x="4" y="20" width="36" height="30" fill="url(#iconGrad)"/><rect x="14" y="52" width="16" height="5" fill="#6a2bd9"/><path d="M22 40 48 14l6 6-26 26h-6z" fill="#1f86dc" stroke="#1e1e1e" stroke-width="2"/><path d="M48 6l8 8-4 4-8-8z" fill="#6a2bd9"/></svg>
    <h3>Custom Graphics</h3>
    <p>Logos, branding, striping, racing lines, special accents—bring your vision to life.</p>
  </div>
  <a class="btn" style="left:498px;top:1722px;width:204px;height:40px"><span>Explore All Services</span></a>

  <!-- Recent work -->
  <h2 class="section-title display grad-text" style="top:1878px">Recent Work</h2>
  <p class="abs work-sub">From daily drivers to exotic builds, we treat every project with the same level of care and craftsmanship.<br>Browse our latest wraps, PPF installs &amp; custom designs.</p>
  <div class="photo" style="left:144px;top:2013px;width:289px;height:229px;background:linear-gradient(160deg,#6c6f66,#8a8a8d 45%,#5a5a5d)" role="img" aria-label="Silver hatchback with orange rust-effect wrap"></div>
  <div class="photo" style="left:455px;top:2013px;width:290px;height:477px;background:linear-gradient(180deg,#8c8a84 0%,#2b2e36 30%,#1d1f24 60%,#3a3a3a 100%)" role="img" aria-label="Black coupe front with bronze racing stripe"></div>
  <div class="photo" style="left:765px;top:2013px;width:290px;height:229px;background:linear-gradient(160deg,#555,#a7a9ab 50%,#6b6b6b)" role="img" aria-label="Silver sedan with red windshield banner"></div>
  <div class="photo" style="left:144px;top:2261px;width:289px;height:229px;background:linear-gradient(160deg,#6b5a48,#2b6c8e 50%,#8a8984)" role="img" aria-label="Blue wrapped sports car outside a garage"></div>
  <div class="photo" style="left:765px;top:2261px;width:290px;height:229px;background:linear-gradient(150deg,#1b3fc9,#2e55d8 50%,#7a7a72)" role="img" aria-label="Blue car rear window with custom lettering decal"></div>
  <a class="btn" style="left:498px;top:2518px;width:204px;height:40px"><span>Explore All Photos</span></a>

  <!-- Testimonials -->
  <div class="abs testi-band" role="img" aria-label="Dim background photo of a car in a workshop"></div>
  <h2 class="section-title display grad-text" style="top:2760px">What Customers Are Saying</h2>
  <div class="abs quote-mark grad-text" style="left:140px;top:2860px">“</div>
  <p class="abs testi-head" style="left:236px;top:2853px">Amazing quality and attention to detail.<br>My car looks brand new!</p>
  <p class="abs testi-body" style="left:236px;top:2909px">“Lorem ipsum dolor sit amet, consectetur adipiscing elit, sed do eiusmod tempor incididunt ut labore et dolore magna aliqua. Lorem ipsum dolor sit amet, consectetur adipiscing elit, sed do”</p>
  <p class="abs testi-name" style="left:236px;top:3015px">John doe<small>Company name</small></p>
  <div class="abs quote-mark grad-text" style="left:633px;top:2860px">“</div>
  <p class="abs testi-head" style="left:729px;top:2853px">Amazing quality and attention to detail.<br>My car looks brand new!</p>
  <p class="abs testi-body" style="left:729px;top:2909px">“Lorem ipsum dolor sit amet, consectetur adipiscing elit, sed do eiusmod tempor incididunt ut labore et dolore magna aliqua. Lorem ipsum dolor sit amet, consectetur adipiscing elit, sed do”</p>
  <p class="abs testi-name" style="left:729px;top:3015px">John doe<small>Company name</small></p>
  <svg class="abs" style="left:60px;top:2938px" width="16" height="20" viewBox="0 0 16 20"><path d="M12 2 4 10l8 8" stroke="#fff" stroke-width="2.5" fill="none"/></svg>
  <svg class="abs" style="left:1120px;top:2938px" width="16" height="20" viewBox="0 0 16 20"><path d="M4 2l8 8-8 8" stroke="#fff" stroke-width="2.5" fill="none"/></svg>

  <!-- Contact form -->
  <h2 class="section-title display grad-text" style="top:3231px">Get In Touch</h2>
  <div class="field" style="left:144px;top:3300px;width:295px;height:62px">Name</div>
  <div class="field" style="left:452px;top:3300px;width:296px;height:62px">Email</div>
  <div class="field" style="left:761px;top:3300px;width:295px;height:62px">Phone</div>
  <div class="field" style="left:144px;top:3380px;width:912px;height:145px">Message</div>
  <a class="btn" style="left:530px;top:3544px;width:140px;height:45px;font-size:14px"><span>SUBMIT NOW</span></a>

  <!-- Footer -->
  <div class="abs footer" role="img" aria-label="Dim background photo of a vehicle front"></div>
  <div class="abs foot-brand"><i></i>Gleam Shell Crew</div>
  <div class="abs foot-col" style="left:387px;top:3776px">
    <h4>Top Services</h4>
    <ul><li>Vinyl Wraps</li><li>Vantor Paint Protection Film</li><li>Matte Paint Protection Film</li><li>Coloured PPF</li><li>Ceramic Coating</li><li>Car Detailing</li><li>Custom Decals</li></ul>
  </div>
  <div class="abs foot-col" style="left:626px;top:3776px">
    <h4>Useful Links</h4>
    <ul><li>Financing</li><li>Gallery</li><li>Blog</li><li>Jobs</li><li>Warranty</li><li>Arcline Owners of Alberta</li><li>Trevane Owners Canada</li></ul>
  </div>
  <div class="abs foot-col" style="left:834px;top:3776px"><h4>Contact</h4></div>
  <div class="contact-row" style="top:3812px">
    <svg width="22" height="20" viewBox="0 0 22 20"><path d="M4 2l4 1 1 4-2 2a11 11 0 0 0 5 5l2-2 4 1 1 4-3 2C9 18 2 11 1 5z" fill="url(#iconGrad)"/></svg>
    <span>+1 888 888 8888</span>
  </div>
  <div class="contact-row" style="top:3860px">
    <svg width="22" height="16" viewBox="0 0 22 16"><rect x="1" y="1" width="20" height="14" fill="url(#iconGrad)"/><path d="M1 1l10 8 10-8" stroke="#141414" stroke-width="1.5" fill="none"/></svg>
    <span>info@companyname.com</span>
  </div>
  <div class="contact-row" style="top:3908px">
    <svg width="22" height="20" viewBox="0 0 22 20"><path d="M11 1a7 7 0 0 1 7 7c0 5-7 11-7 11S4 13 4 8a7 7 0 0 1 7-7z" fill="url(#iconGrad)"/><circle cx="11" cy="8" r="2.5" fill="#141414"/></svg>
    <span>Lorem ipsum dolor sit<br>amet, consectetur</span>
  </div>
  <p class="abs copyright">© &nbsp;Copyrights 2025 | All Rights Reserved</p>

</div>
</body>
</html>
```